Harbor Lanterns Book Cover Design

Book Cover Design Brief:
Title: Harbor Lanterns
Author: Dena Morrow
đź§­ Subtitle:
A Handbook for the Woman in the Storm or Set to Begin
🎯 Badge Text:
A Compass for Women Navigating Transformation
Trim Size: 6 x 9 inches
Total Number of Pages: Estimate 204 pages (including front/back matter and section dividers).
⸻

đź§­ Overview

Harbor Lanterns is a powerful, faith-based guide and story collection written by Dena Morrow who shares stories of 12 other women. Each chapter offers real-life insight and encouragement for women walking through the emotional wilderness of life—divorce, grief, burnout, identity shifts, loss, and uncertainty. This book isn’t about being lost in nature—it’s about navigating the unseen wilderness of the heart and soul, and finding sacred direction through faith, sisterhood, and intentional self-discovery. It’s for the woman who feels alone in what she’s going through, and is ready to rise again—with strength, clarity, and support.
đź§­ The Compass Framework
The book is grounded in Dena Morrow’s Compass Framework: Community, Openness, Mindset, Purposeful Movement, Accountability, Support, and Self-Care. This 7-part model guides readers from feeling lost to finding purpose, and the compass symbol should appear on the cover as a subtle but meaningful visual representing that inner journey.
🎨 Design Direction Must Haves
• A single woman in a wilderness-like setting (open field, mist, shoreline, etc.), visually representing emotional solitude and personal reflection • A compass or symbolic directional element integrated into the design (can be subtle—part of the background, light, path, etc.) •Mood should reflect quiet strength, inner transformation, hope and sacred guidance
Color palette: Deep greens, earthy tones, and warm golden or divine light—evoking grounding, hope, and spiritual depth
Title: Harbor Lanterns
• “Wilderness” in a natural, elegant font (same as The Harbor Lantern logo if possible) “Wisdom” in a bold serif to evoke strength and maturity
đź§­ Subtitle:
Author Name: Dena Morrow (centered or lower third, clean serif font)
Badge Text: 🎯 Badge Text:
(discreet, bottom right or near author name—no drop shadows)

Nice to Haves: Subtle visual cues of sisterhood or support in the distance (faint outlines, footsteps, horizon silhouettes) • Divine light or glow to represent God’s presence • Natural textures like breeze, water, or mist to evoke movement and transition •A sense of forward momentum—even if the woman is standing still
Should Not Have •Literal forest survival imagery •Cold or overly corporate fonts •Harsh primary colors or visual clutter
Back Cover / Spine Note The design should flow naturally into the spine and back cover. The compass and wilderness elements should feel part of the world, not placed on top of it.
Back Cover Description:
Harbor Lanterns is a healing guide and collection of real stories from women who have walked through life’s hardest seasons. Divorce, grief, abandonment, illness, burnout, addiction, estrangement, narcissistic abuse, homelessness, and the loss of loved ones are all part of the emotional wilderness this book speaks to.
If you feel lost, stuck, or unsure of who you are now, you are not alone. This book is for the woman standing in the middle of her wilderness, ready to take the next step toward healing and purpose.
Each chapter offers real truth and practical encouragement, with reflections that point you back to your strength, your True North, and the life you were made for.
Harbor Lanterns helps you reclaim faith, power, and purpose through the Compass Framework, a path shaped by values like community, mindset, and self-care.
Harbor Lanterns is a healing guide and collection of real stories from women who have walked through life’s hardest seasons. Written by life and business coach Dena Morrow, the book shares her personal journey alongside the voices of 12 courageous women. Divorce, grief, abandonment, illness, burnout, addiction, estrangement, narcissistic abuse, homelessness, and the loss of loved ones are all part of the emotional wilderness this book speaks to.

Whether you are standing in the fire or ready to rise from it, this book was written to meet you there. It is for the woman who feels stuck, shaken, or unsure of who she is now and knows something within her is ready to heal.

Each chapter offers truth and encouragement, with reflections that point you back to your strength, your True North, and the life you were made for.

With every page, you are reminded that you are not lost. You are finding your way as you engage with Dena’s story, the experiences of 12 other women, apply the tools, and move forward with clarity and courage.

Author Bio:
Dena Morrow is a life and business coach, speaker, and author who empowers women to reclaim their faith, power, and purpose after life has shaken their foundation. As the founder of The Harbor Lantern, she helps women move forward with clarity and confidence through seasons of change, loss, and transformation.

Through her coaching, workshops, and writing, Dena creates spaces where women stop feeling stuck and start rising, equipped with tools, community, and a renewed sense of direction for the life ahead.

Target Market(s)

Women ages 30-80

Industry/Entity Type

Faith Based Self Help, Spiritual Growth • Christian Living / Women’s Issues • Faith-Based Personal Development • Self-Help / Spiritual • Women’s Empowerment • Personal Transformation

Font styles to use
Serif
Sans Serif

Requirements
Must have
• A cover that visually reflects the emotional wilderness women experience during life transitions—grief, divorce, abandonment, identity loss, loss of loved one, estrangement, addiction, burnout, etc.—and the sacred path toward hope, strength, and purpose • A design that communicates both solitude and resilience, with visual cues that suggest faith, guidance, and transformation • A compass symbol or directional element subtly integrated to represent the Compass Framework (Community, Openness, Mindset, Purposeful Movement, Accountability, Support, Self-Care) • The overall tone should be inspiring, reflective, and spiritually grounded—not clinical, overly modern, or corporate • Designers are encouraged to explore concepts involving a single woman or symbolic imagery that evokes personal journey and inner navigation • Use of natural elements (landscape, light, sky, mist, etc.) is welcomed but not required—designers may propose abstract, minimalist, or layered concepts that align with the book’s message • Include the following text: • Title: Harbor Lanterns • Subtitle: đź§­ Subtitle: A Handbook for the Woman in the Storm or Set to Begin 🎯 Badge Text: A Compass for Women Navigating Transformation • Author: Dena Morrow •If you are using women they need to be real, diverse in age between 30-80 , body type and demographics
Nice to have
• A woman (or symbolic figure) in the design to reflect the personal, emotional journey of transformation • Subtle visual references to faith, sisterhood, or unseen support (e.g., faint silhouettes, glowing light, soft horizon figures, or abstract representations) • Creative use of natural elements like fog, water, paths, or sky to symbolize movement, mystery, or healing • A warm, layered color palette that transitions from darkness or shadow into light—suggesting hope and divine guidance • Textured or painterly backgrounds that feel organic and timeless • Compass elements woven into the environment (not pasted on top)—integrated as part of the visual metaphor • A sense of emotional depth or quiet strength that draws the viewer in • A design that would appeal to a wide age range of women (not too youthful or too somber)
Should not have
• Literal or clichĂ© wilderness imagery that feels like survival gear, camping, or rugged outdoor adventure • Harsh or neon colors, overly bright palettes, or anything that feels “salesy” or corporate • Clip art, cartoon-style illustrations, or flat graphics that lack emotional depth • Fonts that are overly modern, decorative, or hard to read—especially script fonts that look informal or casual • Designs that feel cold, sterile, masculine, or tech-driven • Cluttered layouts or elements that distract from the core message of faith, reflection, and transformation • Any portrayal that makes the woman look hopeless or abandoned—this is a story of resilience and rising, not despair. • A “sorority” or exclusive club feel—this book should never appear as if it’s only for a select group or the “cool girls” • Any design that suggests perfection, status, or elitism—this is about raw, real life, and inner healing • Glamour-focused imagery that disconnects from authenticity or emotional depth

```html
<!DOCTYPE html>
<html lang="en">
<head>
<meta charset="utf-8">
<title>Harbor Lanterns — Cover Spread</title>
<link rel="stylesheet" href="https://fonts.googleapis.com/css2?family=Jost:wght@300;400&family=Open+Sans:wght@400&family=EB+Garamond:wght@400&display=swap">
<style>
  :root{
    --stage:#4a4a4a;
    --paper:#fdfaf1;
    --teal:#4f97a2;
    --ink:#1f1f1f;
    --body:#6b6b6b;
    --gold-light:#dcb965;
    --gold-dark:#b8892f;
    --scene-sky:#a9c9cc;
    --scene-water:#5f949c;
    --scene-green:#4f6f4c;
  }
  *{box-sizing:border-box;margin:0;padding:0}
  html,body{width:1200px;height:1200px;overflow:hidden;background:var(--stage)}
  .spread{
    position:absolute;left:40px;top:200px;width:1120px;height:801px;
    background:var(--paper);overflow:hidden;
  }
  /* back cover */
  .back{position:absolute;left:0;top:0;width:530px;height:100%}
  .back-title{
    position:absolute;left:50px;top:100px;width:434px;text-align:center;
    font-family:"Jost",sans-serif;font-weight:400;font-size:44px;line-height:1.1;color:var(--teal);
    letter-spacing:0.5px;white-space:nowrap;
  }
  .back-subtitle{
    position:absolute;left:50px;top:152px;width:434px;text-align:center;
    font-family:"Jost",sans-serif;font-weight:400;font-size:13.6px;line-height:1.3;color:var(--ink);
    white-space:nowrap;
  }
  .blurb,.bio,.blurb-close{
    position:absolute;font-family:"Open Sans",sans-serif;font-size:11.3px;line-height:16.1px;
    color:var(--body);text-align:justify;text-align-last:center;
  }
  .blurb{left:50px;top:178px;width:434px}
  .bio{left:172px;top:396px;width:312px;text-align-last:left}
  .blurb-close{left:50px;top:514px;width:434px;text-align-last:left}
  .author-photo{
    position:absolute;left:48px;top:398px;width:107px;height:107px;border-radius:50%;
    background:radial-gradient(circle at 50% 40%,#d9b9a0 0%,#7a5a48 45%,#d6a63c 85%);
  }
  .imprint{
    position:absolute;left:50px;top:722px;display:flex;align-items:center;gap:8px;
    font-family:"Jost",sans-serif;font-weight:400;font-size:22px;color:var(--ink);letter-spacing:1px;
  }
  .imprint-dot{width:12px;height:12px;border:1.5px solid var(--ink);border-radius:50%}
  /* spine */
  .spine{position:absolute;left:530px;top:0;width:58px;height:100%}
  .spine-text{
    position:absolute;left:50%;transform:translateX(-50%);
    writing-mode:vertical-rl;font-family:"Jost",sans-serif;white-space:nowrap;line-height:1;
  }
  .spine-title{top:32px;font-size:20px;color:var(--teal);letter-spacing:0.5px}
  .spine-subtitle{top:270px;font-size:10.4px;color:var(--ink)}
  .spine-mark{position:absolute;left:21px;top:627px;width:16px;height:16px;border:1.5px solid var(--ink);border-radius:50%}
  .spine-author{top:654px;font-size:14px;color:var(--ink);letter-spacing:1.5px}
  /* front cover */
  .front{position:absolute;left:588px;top:0;width:532px;height:100%}
  .front-subtitle{
    position:absolute;left:0;top:56px;width:100%;text-align:center;
    font-family:"Jost",sans-serif;font-size:15.6px;color:var(--ink);white-space:nowrap;
  }
  .front-title{
    position:absolute;left:0;top:80px;width:100%;text-align:center;
    font-family:"Jost",sans-serif;font-weight:400;color:var(--teal);line-height:1;
  }
  .front-title .line{display:block;white-space:nowrap}
  .front-title .line-one{font-size:84px;letter-spacing:1px}
  .front-title .line-two{font-size:98px;letter-spacing:0}
  .cover-scene{
    position:absolute;left:40px;top:262px;width:480px;height:539px;
    background:
      radial-gradient(ellipse 60% 55% at 60% 42%,var(--scene-sky) 0%,rgba(169,201,204,0.6) 55%,rgba(253,250,241,0) 100%),
      radial-gradient(ellipse 40% 35% at 55% 78%,var(--scene-water) 0%,rgba(95,148,156,0.5) 60%,rgba(253,250,241,0) 100%),
      radial-gradient(ellipse 30% 22% at 45% 100%,var(--scene-green) 0%,rgba(79,111,76,0) 100%);
  }
  .front-author{
    position:absolute;left:44px;top:726px;
    font-family:"Jost",sans-serif;font-size:25px;color:var(--ink);letter-spacing:2.5px;white-space:nowrap;
  }
  .badge{
    position:absolute;left:372px;top:642px;width:116px;height:116px;border-radius:50%;
    background:radial-gradient(circle at 40% 35%,var(--gold-light) 0%,var(--gold-dark) 100%);
    display:flex;align-items:center;justify-content:center;text-align:center;
    font-family:"EB Garamond",serif;font-size:13px;line-height:16.5px;color:#fffaf0;padding:0 10px;
  }
</style>
</head>
<body>
<main class="spread">
  <section class="back">
    <h2 class="back-title">HARBOR LANTERNS</h2>
    <p class="back-subtitle">A HANDBOOK FOR THE WOMAN IN THE STORM OR SET TO BEGIN</p>
    <p class="blurb">Lorem ipsum dolor sit amet, consectetur adipiscing elit, sed do eiusmod tempor incididunt ut labore et dolore magna aliqua. Quis ipsum suspendisse ultrices gravida. Risus commodo viverra maecenas accumsan lacus vel facilisis. Lorem ipsum dolor sit amet, consectetur adipiscing elit, sed do eiusmod tempor incididunt ut labore et dolore magna aliqua. Quis ipsum suspendisse ultrices gravida. Risus commodo viverra maecenas accumsan lacus vel facilisis. Lorem ipsum dolor sit amet, consectetur adipiscing elit, sed do eiusmod tempor incididunt ut labore et dolore magna aliqua. Quis ipsum suspendisse ultrices gravida. Risus commodo viverra maecenas accumsan lacus vel facilisis. Lorem ipsum dolor sit amet, consectetur adipiscing elit, sed do eiusmod tempor incididunt ut labore et dolore magna aliqua. Quis ipsum suspendisse ultrices gravida. Risus commodo viverra maecenas accumsan lacus vel facilisis.</p>
    <div class="author-photo" role="img" aria-label="Portrait photograph of author Dena Morrow"></div>
    <p class="bio">Lorem ipsum dolor sit amet, consectetur adipiscing elit, sed do eiusmod tempor incididunt ut labore et dolore magna aliqua. Quis ipsum suspendisse ultrices gravida. Risus commodo viverra maecenas accumsan lacus vel facilisis. Lorem ipsum dolor sit amet, consectetur adipiscing elit, sed do eiusmod tempor incididunt ut labore et dolore magna aliqua. Quis ipsum suspendisse</p>
    <p class="blurb-close">Lorem ipsum dolor sit amet, consectetur adipiscing elit, sed do eiusmod tempor incididunt ut labore et dolore magna aliqua. Quis ipsum suspendisse ultrices gravida. Risus commodo viverra maecenas accumsan lacus vel facilisis.</p>
    <div class="imprint"><span class="imprint-dot"></span>The Harbor Lantern</div>
  </section>

  <section class="spine">
    <span class="spine-text spine-title">HARBOR LANTERNS</span>
    <span class="spine-text spine-subtitle">A HANDBOOK FOR THE WOMAN IN THE STORM OR SET TO BEGIN</span>
    <span class="spine-mark"></span>
    <span class="spine-text spine-author">DENA MORROW</span>
  </section>

  <section class="front">
    <p class="front-subtitle">A HANDBOOK FOR THE WOMAN IN THE STORM OR SET TO BEGIN</p>
    <h1 class="front-title">
      <span class="line line-one">HARBOR</span>
      <span class="line line-two">LANTERNS</span>
    </h1>
    <div class="cover-scene" role="img" aria-label="Double-exposure illustration: a woman's profile silhouette filled with a misty mountain lake landscape, set over a pale compass rose"></div>
    <p class="front-author">DENA MORROW</p>
    <div class="badge">A<br>Compass for<br>Women<br>Navigating<br>Transformation</div>
  </section>
</main>
</body>
</html>
```